Stationery Design Project for Nimbora, Chicago

Nimbora, a street parking application which helps car drivers find a street parking spot by offering an ideal path along which to look for parking. This path is calculated by our algorithm based on data (e.g. historical data, baseball games schedule, etc.). Along this path the driver will find a spot and will also save 70% of the search time. Customer we target is reg. between 21 and 45 yo.

We envision something young, fresh, bright and original. Slightly abstract maybe. It should represent the idea and elements of finding street parking in the city, e.g. car(s), parking spot, people, city, etc. (just ideas!).

Logo is attached.

Requirement:
- Business Cards (2 Sided Full Color CMYK)
- Letterhead (1 Sided Full Color CMYK)
- Envelope (1 Sided Full Color CMYK)
- Sticker (1 Sided Full Color CMYK), round with a 2inch diameter.

Reason: We're starting to get more and more designs and need more time to look into all of them. Very exciting!! Thanks to everybody!

Hi all, we're in the process of selecting our favs. Though choices!!! Really good submissions. Will keep you posted and sorry for the delay.

Target Market(s)

Car drivers and owners between 21 and 45

Industry/Entity Type

Parking

Requirements
Must have
• Sticker should be round and include company URL nimbora.com and the new logo which we will attach soon.
Should not have
• Should not be too serious or boring.

```html
<!DOCTYPE html>
<html lang="en">
<head>
<meta charset="utf-8">
<title>Nimbora — Business Card</title>
<link href="https://fonts.googleapis.com/css2?family=Open+Sans:wght@400;600;700&display=swap" rel="stylesheet">
<style>
  :root {
    --stage: #e4e4e6;
    --card: #ffffff;
    --ink: #1c1c1e;
    --ink-soft: #444446;
    --name-grey: #58585a;
    --rule: #555557;
    --mark-blue: #1f5fc9;
    --sky-top: #c4cbd3;
    --sky-low: #e2e5e8;
    --trees-dark: #4a6a3f;
    --trees: #6f8a5c;
    --walkway: #c9c3b8;
    --lot-warm: #8a7270;
    --lot: #6f7174;
    --lot-dark: #55575a;
  }
  * { margin: 0; padding: 0; box-sizing: border-box; }
  html, body { width: 956px; height: 1200px; overflow: hidden; }
  body {
    position: relative;
    background: var(--stage);
    font-family: "Open Sans", sans-serif;
    color: var(--ink);
  }
  .card {
    position: absolute;
    border-radius: 28px;
    overflow: hidden;
    box-shadow: 0 6px 18px rgba(0,0,0,0.25);
  }
  .card-front { left: 79px; top: 90px; width: 798px; height: 455px; background: var(--card); }
  .card-back { left: 96px; top: 638px; width: 797px; height: 454px; }

  .brand { position: absolute; display: flex; align-items: center; }
  .brand-dot { border-radius: 50%; background: var(--mark-blue); flex: none; }
  .brand-name { font-weight: 600; color: var(--ink); letter-spacing: -1px; line-height: 1; }

  .card-front .brand { left: 127px; top: 37px; }
  .card-front .brand-dot { width: 156px; height: 156px; margin-right: 28px; }
  .card-front .brand-name { font-size: 96px; }

  .holder { position: absolute; left: 0; width: 100%; top: 210px; text-align: center; padding-left: 32px; color: var(--name-grey); font-weight: 700; font-size: 24px; }
  .holder .role { font-size: 19px; }

  .contact-phones { position: absolute; right: 427px; top: 315px; text-align: right; font-size: 22px; line-height: 36px; color: var(--ink-soft); }
  .contact-phones b, .contact-web b { color: var(--ink); }
  .contact-divider { position: absolute; left: 388px; top: 298px; width: 2px; height: 100px; background: var(--rule); }
  .contact-address { position: absolute; left: 403px; top: 322px; font-size: 22px; line-height: 31px; color: var(--ink-soft); }
  .contact-web { position: absolute; left: 0; width: 100%; top: 405px; text-align: center; padding-right: 24px; font-size: 22px; color: var(--ink-soft); }

  .scene-photo {
    position: absolute; inset: 0;
    background: linear-gradient(to bottom,
      var(--sky-top) 0%, var(--sky-low) 26%,
      var(--trees) 30%, var(--trees-dark) 40%,
      var(--walkway) 45%, var(--lot-warm) 52%,
      var(--lot) 70%, var(--lot-dark) 100%);
  }
  .card-back .brand { left: 212px; top: 24px; }
  .card-back .brand-dot { width: 104px; height: 104px; margin-right: 18px; }
  .card-back .brand-name { font-size: 64px; }
</style>
</head>
<body>
  <section class="card card-front">
    <div class="brand">
      <span class="brand-dot"></span>
      <span class="brand-name">Nimbora</span>
    </div>
    <p class="holder">Your Name - <span class="role">Designation</span></p>
    <div class="contact-phones">
      <div><b>t</b> : 123-456-7890</div>
      <div><b>c</b> : 123-456-7890</div>
    </div>
    <span class="contact-divider"></span>
    <div class="contact-address">
      <div>City Name, Street Name</div>
      <div>State Name, Country Code</div>
    </div>
    <p class="contact-web"><b>e</b> : name@website.com &nbsp;<b>w</b> : www.website.com</p>
  </section>

  <section class="card card-back">
    <div class="scene-photo" role="img" aria-label="Photograph of a busy city car park: rows of parked cars in marked bays on grey asphalt, a fenced walkway and trees behind, under an overcast sky"></div>
    <div class="brand">
      <span class="brand-dot"></span>
      <span class="brand-name">Nimbora</span>
    </div>
  </section>
</body>
</html>
```